Values and Organizational Purpose Signage

We recently solidified our company values, organizatioanal purpose and strategic vision. I'd like to develop some tasteful (not overly corporate) signage of these values to display in our office.

I've attached the hand-written values and purpose that my core team members then initialed acknowleding they align along with the signage at the front of our office to provide some perspective on our brand identity.

Industry/Entity Type

It Company

Font styles to use
Sans Serif

Requirements
Must have
• I'd like to see the values and org purpose depicted as one sign and as separate signs (i.e., values on one sign and org purpose on another). I need it to reflect our brand identity which I've uploaded

```html
<!DOCTYPE html>
<html lang="en">
<head>
<meta charset="utf-8">
<title>Core Values Sign</title>
<link rel="stylesheet" href="https://fonts.googleapis.com/css2?family=Caladea:wght@400;700&display=swap">
<style>
  :root {
    --frame: #454f5a;
    --paper: #ffffff;
    --lime: #c6d632;
    --slate: #3f4955;
    --stone: #5b5b5d;
    --rule: #6b6b6b;
    --hairline: #8a8a8a;
  }
  * { margin: 0; padding: 0; box-sizing: border-box; }
  html, body {
    width: 730px;
    height: 1200px;
    overflow: hidden;
    background: var(--frame);
  }
  .sign {
    position: relative;
    width: 730px;
    height: 1200px;
    background: var(--frame);
    font-family: "Caladea", "Cambria", Georgia, serif;
  }
  .sign-panel {
    position: absolute;
    left: 12px;
    top: 12px;
    right: 10px;
    bottom: 0;
    background: var(--paper);
  }
  .sign-title {
    position: absolute;
    left: 90px;
    top: 52px;
    font-size: 86px;
    font-weight: 400;
    line-height: 115px;
    color: var(--lime);
    letter-spacing: 0.5px;
  }
  .sign-title-rule {
    position: absolute;
    left: 90px;
    top: 275px;
    width: 504px;
    height: 3px;
    background: var(--rule);
  }
  .value-note {
    position: absolute;
    left: 91px;
    width: 580px;
    font-size: 27px;
    line-height: 31px;
    color: var(--lime);
  }
  .value-note::before {
    content: "";
    position: absolute;
    left: -11px;
    top: 2px;
    width: 1.5px;
    height: var(--tick, 58px);
    background: var(--hairline);
  }
  .value-name {
    position: absolute;
    left: 32px;
    font-size: 60px;
    line-height: 1;
    color: var(--slate);
    white-space: nowrap;
  }
  .value-name .initial {
    font-size: 80px;
  }
  .value-name.is-stone { color: var(--stone); }

  .brand-name {
    position: absolute;
    left: 0;
    right: 0;
    top: 1120px;
    text-align: center;
    font-size: 26px;
    line-height: 1;
    color: var(--slate);
    letter-spacing: 2px;
  }
</style>
</head>
<body>
<main class="sign">
  <div class="sign-panel">
    <h1 class="sign-title">Core Values<br>Defines</h1>
    <div class="sign-title-rule"></div>

    <p class="value-note" style="top: 367px;">We are transparent and receptive to the thoughts, opinions, and feelings to others</p>
    <h2 class="value-name is-stone" style="top: 445px;"><span class="initial">R</span>espect</h2>

    <p class="value-note" style="top: 592px; --tick: 32px;">We uphold our promises</p>
    <h2 class="value-name" style="top: 603px;"><span class="initial">I</span>ntegrity</h2>

    <p class="value-note" style="top: 749px;">We continuously strive to be the best in all endeavors</p>
    <h2 class="value-name" style="top: 797px;"><span class="initial">E</span>xcellence</h2>

    <p class="value-note" style="top: 932px; --tick: 40px;">We encourage creative and innovative expressions</p>
    <h2 class="value-name" style="top: 984px;"><span class="initial">O</span>pen mindedness</h2>

    <div class="brand-name">Nortavia</div>
  </div>
</main>
</body>
</html>
```